International MLM Business needs Coffee Packaging Design

We are an MLM Company engaged in selling Food Supplements to our independent distributors.

We need a Packaging Design for our Instant Coffee (Cafe Latte) enhanced with Food Supplement (Ganoderma and Goji Powder)

Sachet Material is PET/AL/PE
Sachet Size is 45mm x 160mm (L x H) (FORMED)
Canvass Size is 110mm x 160mm (L x H) (FLAT)

The packaging design requirements are as follows:

1. Design must be in upright position (portrait).

2. We would like to see "VELTORIQ" (our brand logo) included in the design. See uploaded file.

3. We also would like to see some "gold" touch in the label.

4. The coffee is part of our "SUPER" series.

5. Include "PREMIUM COFFEE", "WITH GANODERMA & GOJI EXTRACT" as our main selling point.

6. Add Net Weight at the lower right portion. Net Weight is 25 grams.

7. Add Serving Instruction at the Back.

1. Empty 1 sachet of VELTORIQ Super Cafe Latte into a mug.
2. Fill the mug with 220ml of hot water (80 degrees celsius) and stir. (Use "80oc")
I don't know how to superscript the "o".
3. Enjoy a rich, healthy VELTORIQ Super Cafe Latte.

8. Add Ingredients at the Back.

"Sugar, Non Dairy Creamer, Pure Instant Coffee, Organic Goji Extract, Organic Ganoderma Extract."

9. Add Best Before Date at the Back.

10. Add Manufacturer Details at the Back.

Our website is http://www.veltoriq-example.com

*attached photo is for presentation purposes only. It's up to you to design.*

Designer Payment changed to committed. We are very serious about this project. So please kindly submit all entries. Thanks!

```html
<!DOCTYPE html>
<html lang="en">
<head>
<meta charset="utf-8">
<title>VELTORIQ Premium Coffee Latte – Sachet Front and Back</title>
<link rel="stylesheet" href="https://fonts.googleapis.com/css2?family=Arimo:wght@400;700&family=Roboto+Condensed:wght@400;700&display=swap">
<style>
  :root {
    --bg: #e4e4e4;
    --brown-dark: #2a1710;
    --brown-mid: #3d2418;
    --brown-edge: #1c0f0a;
    --tan-light: #d9a468;
    --tan: #b9783f;
    --tan-deep: #8a5328;
    --cream: #f6dcb4;
    --cream-light: #fbeedb;
    --gold: #e9b64e;
    --gold-deep: #b88424;
    --green: #8cc63f;
    --text-light: #f3e6d4;
    --text-muted: #c9a57a;
  }
  * { margin: 0; padding: 0; box-sizing: border-box; }
  html, body { width: 910px; height: 1200px; overflow: hidden; }
  body {
    background: var(--bg);
    font-family: "Arimo", Arial, sans-serif;
    position: relative;
  }
  .sachet {
    position: absolute;
    top: 50px;
    width: 320px;
    height: 1100px;
    background: var(--brown-dark);
    overflow: hidden;
    box-shadow: 0 6px 20px rgba(0,0,0,.25);
  }
  .sachet--front { left: 110px; }
  .sachet--back { left: 480px; }

  .crimp {
    position: absolute;
    left: 0; right: 0;
    height: 42px;
    background: repeating-linear-gradient(90deg, var(--brown-mid) 0 3px, var(--brown-edge) 3px 6px);
  }
  .crimp--top { top: 0; }
  .crimp--bottom { bottom: 0; }

  .gold-band {
    position: absolute;
    left: 0; right: 0;
    background: linear-gradient(90deg, var(--tan-deep) 0%, var(--tan) 25%, var(--tan-light) 55%, var(--tan) 80%, var(--tan-deep) 100%);
  }

  /* Front */
  .brand {
    position: absolute;
    top: 210px; left: 0; right: 0;
    display: flex; align-items: center; justify-content: center; gap: 10px;
  }
  .brand__dot { width: 26px; height: 26px; border-radius: 50%; background: var(--green); }
  .brand__name { color: var(--green); font-size: 34px; font-weight: 400; letter-spacing: 0.5px; }

  .front-band { top: 330px; height: 440px; }
  .title-premium {
    position: absolute; top: 385px; left: 0; right: 0;
    text-align: center; font-weight: 700; font-size: 42px;
    color: var(--brown-dark);
  }
  .title-lettering {
    position: absolute; top: 445px; left: 40px; width: 240px; height: 110px;
    border-radius: 40px;
    background: radial-gradient(ellipse at center, var(--cream-light) 0%, var(--cream) 60%, rgba(246,220,180,0) 100%);
  }
  .title-latte {
    position: absolute; top: 558px; left: 0; right: 0;
    text-align: center; font-weight: 700; font-size: 46px;
    color: var(--brown-dark);
  }
  .splash {
    position: absolute; top: 620px; left: 0; right: 0; height: 180px;
    background: radial-gradient(ellipse 70% 60% at 50% 70%, #5a2f18 0%, #3a1c0e 55%, rgba(42,23,16,0) 100%);
  }
  .super-badge {
    position: absolute; top: 830px; left: 105px; width: 110px; height: 90px;
    border-radius: 50%;
    background: radial-gradient(circle, var(--gold) 0%, var(--gold-deep) 100%);
  }
  .claim {
    position: absolute; top: 935px; left: 0; right: 0;
    text-align: center; color: var(--gold);
    font-weight: 700; font-size: 22px; line-height: 1.2;
  }
  .net-weight {
    position: absolute; top: 840px; left: 290px;
    transform: rotate(90deg); transform-origin: left top;
    color: var(--text-light); font-weight: 700; font-size: 17px; white-space: nowrap;
  }
  .net-weight strong { font-size: 22px; }

  /* Back */
  .back-band { top: 200px; height: 470px; }
  .back-copy {
    position: absolute; top: 240px; left: 40px; right: 34px;
    font-family: "Roboto Condensed", Arial, sans-serif;
    color: var(--text-light); font-size: 14px; line-height: 1.35;
  }
  .back-copy h2 { font-size: 15px; font-weight: 700; margin-bottom: 6px; }
  .steps { list-style: none; margin-bottom: 12px; }
  .steps li { display: flex; gap: 8px; margin-bottom: 5px; }
  .steps li span { flex: none; width: 10px; }
  .ingredients { margin-bottom: 22px; }
  .step-icons { display: flex; gap: 10px; }
  .step-icon {
    width: 76px; height: 70px;
    border: 2px solid var(--tan-deep);
    background: linear-gradient(180deg, var(--tan-light), var(--tan));
  }
  .back-info {
    position: absolute; top: 760px; left: 40px; right: 30px;
    font-family: "Roboto Condensed", Arial, sans-serif;
  }
  .best-before { color: var(--text-muted); font-size: 17px; line-height: 1.2; margin-bottom: 22px; }
  .maker-label { color: var(--text-light); font-size: 14px; font-weight: 700; }
  .maker-name { color: var(--text-light); font-size: 20px; font-weight: 700; margin-bottom: 6px; }
  .website { color: var(--text-muted); font-size: 14px; letter-spacing: 1.5px; font-weight: 700; }
</style>
</head>
<body>

<section class="sachet sachet--front" aria-label="Sachet front">
  <div class="crimp crimp--top"></div>
  <div class="brand">
    <span class="brand__dot"></span>
    <span class="brand__name">veltoriq</span>
  </div>
  <div class="gold-band front-band"></div>
  <div class="title-premium">Premium</div>
  <div class="title-lettering" role="img" aria-label="Hand-lettered word Coffee in cream script"></div>
  <div class="title-latte">Latte</div>
  <div class="splash" role="img" aria-label="Illustration of a splashing cup of coffee"></div>
  <div class="super-badge" role="img" aria-label="Super Series seal with goji berries and ganoderma"></div>
  <p class="claim">WITH GANODERMA<br>&amp; GOJI EXTRACT</p>
  <p class="net-weight">Net W <strong>25</strong> gms.</p>
  <div class="crimp crimp--bottom"></div>
</section>

<section class="sachet sachet--back" aria-label="Sachet back">
  <div class="crimp crimp--top"></div>
  <div class="gold-band back-band"></div>
  <div class="back-copy">
    <h2>SERVING INSTRUCTION</h2>
    <ol class="steps">
      <li><span>1</span>Empty 1 sachet of VELTORIQ Super Cafe Latte into a mug.</li>
      <li><span>2</span>Fill the mug with 220ml of hot water (80 degrees celsius)</li>
      <li><span>3</span>Enjoy a rich, healthy VELTORIQ Super Cafe Latte.</li>
    </ol>
    <h2>INGREDIENTS</h2>
    <p class="ingredients">"Sugar, Non Dairy Creamer, Pure Instant Coffee, Organic Goji Extract, Organic Ganoderma Extract."</p>
    <div class="step-icons">
      <div class="step-icon" role="img" aria-label="Step drawing: pouring sachet into a mug"></div>
      <div class="step-icon" role="img" aria-label="Step drawing: adding hot water"></div>
      <div class="step-icon" role="img" aria-label="Step drawing: stirring the latte"></div>
    </div>
  </div>
  <div class="back-info">
    <p class="best-before">Best before Dec 2015<br>Best before Dec 2015</p>
    <p class="maker-label">Manufacturer by:</p>
    <p class="maker-name">Companey Name Here</p>
    <p class="website">www.veltoriq-example.com</p>
  </div>
  <div class="crimp crimp--bottom"></div>
</section>

</body>
</html>
```